Website Design - TallyPorchHelpers.net

PLEASE CHECK WORD DOCUMENT ATTACHED FOR WEBSITE FLOW.

Target Market(s)

REAL ESTATE AGENTS ARE THE TARGET MARKET

Industry/Entity Type

Real Estate

Coding

Coded - Design and coding required

Number of Pages Required

4 page

Colors

Designer to choose colors to be used in the design.

Requirements
Must have
• WE LIKE RED LOGO ATTACHED
Nice to have
• PLEASE CHECK WORD DOCUMENT ATTACHED FOR WEBSITE FLOW.
Should not have

```html
<!DOCTYPE html>
<html lang="en">
<head>
<meta charset="utf-8">
<title>TallyPorchHelpers.net</title>
<link href="https://fonts.googleapis.com/css2?family=Poppins:wght@500;600;700&family=Roboto:wght@400;500;700&display=swap" rel="stylesheet">
<style>
:root{
  --red:#e8141b;
  --red-deep:#c80d12;
  --ink:#1d1d1d;
  --muted:#555;
  --paper:#f1f1f1;
  --white:#fff;
  --footer:#1b1b1b;
  --footer-text:#a9a9a9;
}
*{margin:0;padding:0;box-sizing:border-box}
html,body{width:718px;height:1200px;overflow:hidden}
body{position:relative;font-family:"Roboto",sans-serif;color:var(--ink);background:var(--white)}
.abs{position:absolute;z-index:2}
.abs.band{z-index:0}
h1,h2,h3{font-family:"Poppins",sans-serif}

/* header */
.site-header{left:0;top:0;width:718px;height:48px;background:var(--white)}
.brand{left:140px;top:9px;display:flex;align-items:center;gap:5px;font-weight:700;font-size:10px;color:var(--red);line-height:1.05;text-transform:uppercase}
.brand-mark{width:10px;height:10px;background:var(--red)}
.main-nav{left:236px;top:20px;display:flex;gap:18px;font-size:6.4px;font-weight:400;letter-spacing:.2px}
.call{left:491px;top:15px;display:flex;align-items:center;gap:5px}
.call small{display:block;font-size:6px;color:var(--muted)}
.call strong{display:block;font-size:8.6px;color:var(--red);font-weight:700}

/* hero */
.hero{left:0;top:48px;width:718px;height:310px;background:linear-gradient(100deg,#2c3224 0%,#5a2a22 30%,#3d3d30 60%,#26301f 100%)}
.hero-text{left:0;top:176px;width:718px;text-align:center;color:var(--white);text-shadow:0 1px 3px rgba(0,0,0,.5)}
.hero-text h1{font-size:19px;font-weight:700;letter-spacing:-.2px}
.hero-text p{font-size:10.6px;font-weight:500;line-height:1.3;margin-top:6px}

/* audience */
.audience{left:0;top:358px;width:718px;height:124px;background:linear-gradient(180deg,#e8141b,#d90f15)}
.audience-title{left:0;top:386px;width:718px;text-align:center;color:var(--white);font-size:11.2px;font-weight:600}
.option{top:419px;width:139px;height:86px;background:var(--white);border-radius:2px;box-shadow:0 3px 8px rgba(0,0,0,.15);text-align:center;overflow:hidden}
.option svg.icon{margin-top:13px}
.option p{font-size:7.4px;line-height:1.3;margin-top:3px}
.option p b{font-weight:700}
.option .stripe{position:absolute;left:0;bottom:0;width:139px;height:11px}

/* packages */
.packages{left:0;top:482px;width:718px;height:368px;background:var(--paper)}
.packages-title{left:0;top:547px;width:718px;text-align:center;font-size:11.6px;font-weight:600}
.plan{top:581px;width:83px;height:225px;background:var(--white);box-shadow:0 2px 6px rgba(0,0,0,.1)}
.plan-head{position:absolute;left:0;top:0;width:83px;height:42px}
.plan-name{position:absolute;left:0;top:10px;width:83px;text-align:center;font-size:8.2px;font-weight:700}
.plan ul{position:absolute;left:8px;top:48px;width:70px;list-style:none;font-size:6px;line-height:1.5;color:#333}
.plan li{position:relative;padding-left:7px;margin-bottom:8px}
.plan li svg{position:absolute;left:0;top:1.5px}
.plan .btn{position:absolute;left:8px;top:168px;width:67px;height:18px;background:#111;color:var(--white);font-size:6.2px;font-weight:700;display:flex;align-items:center;justify-content:center}
.plan.featured .btn{background:var(--red)}
.plan .note{position:absolute;left:4px;top:192px;width:75px;text-align:center;font-size:4.8px;line-height:1.55;color:#666}

/* news */
.news{left:0;top:850px;width:359px;height:190px;background:var(--white)}
.news-title{left:140px;top:871px;font-size:11.6px;font-weight:600}
.news-item{left:140px;width:220px;height:60px}
.thumb{position:absolute;left:0;top:0;width:80px;height:52px}
.news-body{position:absolute;left:91px;top:0;width:115px}
.news-body h3{font-family:"Roboto",sans-serif;font-size:8px;font-weight:400}
.news-meta{font-size:5px;color:#555;margin-top:3px}
.news-meta b{color:var(--red);font-weight:500}
.news-body p{font-size:5.8px;line-height:1.65;color:#666;margin-top:7px}

/* testimonials */
.testimonials{left:359px;top:850px;width:359px;height:190px;background:linear-gradient(90deg,#e8141b 35%,#d41a1c 70%,#c8201f 100%)}
.testimonials-title{left:376px;top:871px;font-size:11.6px;font-weight:600;color:var(--white)}
.quote-mark{left:374px;top:893px;color:#ffb3b3;font-family:"Poppins",sans-serif;font-size:18px;line-height:1}
.quote{left:393px;top:896px;width:186px;font-size:5.9px;line-height:1.8;color:var(--white)}
.avatar{left:393px;top:985px;width:33px;height:33px;border-radius:50%;border:2px solid var(--white);background:radial-gradient(circle at 50% 40%,#e7c8b4,#8a6f60)}
.author{left:433px;top:992px;color:var(--white)}
.author b{display:block;font-size:8px;font-weight:700}
.author span{display:block;font-size:6px;margin-top:2px;padding-left:4px}
.dots{left:548px;top:1013px;display:flex;gap:2.5px}
.dots i{width:4.5px;height:4.5px;border-radius:50%;border:1px solid var(--white)}
.dots i.on{background:var(--white)}

/* footer */
.site-footer{left:0;top:1040px;width:718px;height:160px;background:var(--footer)}
.footer-col{top:1062px;color:var(--footer-text)}
.footer-col h4{font-size:6.8px;font-weight:500;color:var(--white);margin-bottom:8px}
.footer-col p,.footer-col li{font-size:5.8px;line-height:1.75}
.footer-col ul{list-style:none}
.footer-col li{margin-bottom:2px}
.field{background:var(--white);border-radius:1px;font-size:5.4px;color:#aaa;padding:5px 6px}
.send{background:var(--red);color:var(--white);font-size:6px;font-weight:700;display:flex;align-items:center;justify-content:center}
.legal{top:1169px;font-size:6.2px;color:var(--footer-text)}
</style>
</head>
<body>

<header class="site-header abs">
  <div class="brand abs"><span class="brand-mark"></span><span>Tally Porch<br>Helpers</span></div>
  <nav class="main-nav abs">
    <span>HOW IT WORKS</span><span>SERVICE AREA</span><span>PRICING</span><span>ABOUT US</span><span>FAQ</span>
  </nav>
  <div class="call abs">
    <svg width="14" height="14" viewBox="0 0 24 24"><path d="M6.6 10.8a15.1 15.1 0 0 0 6.6 6.6l2.2-2.2a1 1 0 0 1 1-.25 11.4 11.4 0 0 0 3.6.57 1 1 0 0 1 1 1V20a1 1 0 0 1-1 1A17 17 0 0 1 3 4a1 1 0 0 1 1-1h3.5a1 1 0 0 1 1 1c0 1.25.2 2.45.57 3.570a1 1 0 0 1-.25 1z" fill="none" stroke="#e8141b" stroke-width="1.6"/></svg>
    <div><small>Call Us Today</small><strong>1800 555 0142</strong></div>
  </div>
</header>

<section class="hero abs band" role="img" aria-label="Photo of a red open house arrow sign on a lawn in front of a brick house"></section>
<div class="hero-text abs">
  <h1>Helping agents save time and money.</h1>
  <p>We place signs and boost foot traffic to your open houses<br>using proven marketing techniques.</p>
</div>

<section class="audience abs band"></section>
<section class="packages abs band"></section>
<section class="news abs band"></section>
<section class="testimonials abs band" role="img" aria-label="Red tinted photo of a smiling woman behind the testimonials"></section>
<footer class="site-footer abs band"></footer>

<h2 class="audience-title abs">Choose The Option Below That Best Describes You</h2>

<div class="option abs" style="left:140px">
  <svg class="icon" width="22" height="24" viewBox="0 0 22 24"><circle cx="11" cy="7" r="6" fill="#e8141b"/><path d="M0 24a11 9 0 0 1 22 0z" fill="#e8141b"/></svg>
  <p>I'M A<br><b>FULL ON BROKERAGE</b></p>
  <svg class="stripe" viewBox="0 0 139 11" preserveAspectRatio="none"><path d="M0 11V5L139 0v11z" fill="#e8141b"/></svg>
</div>
<div class="option abs" style="left:290px">
  <svg class="icon" width="26" height="24" viewBox="0 0 26 24"><circle cx="6" cy="8" r="3.5" fill="#e8141b"/><circle cx="20" cy="8" r="3.5" fill="#e8141b"/><circle cx="13" cy="6" r="4.5" fill="#e8141b"/><path d="M0 20a6 6 0 0 1 9-5v5z M26 20a6 6 0 0 0-9-5v5z" fill="#e8141b"/><path d="M5 22a8 8 0 0 1 16 0z" fill="#e8141b"/></svg>
  <p>I'M AN<br><b>IND. BROKER WITH A TEAM</b></p>
  <svg class="stripe" viewBox="0 0 139 11" preserveAspectRatio="none"><path d="M0 11V5L139 0v11z" fill="#e8141b"/></svg>
</div>
<div class="option abs" style="left:439px">
  <svg class="icon" width="24" height="24" viewBox="0 0 24 24"><rect x="1" y="0" width="2.5" height="24" fill="#e8141b"/><rect x="20.5" y="0" width="2.5" height="24" fill="#e8141b"/><rect x="3.5" y="2" width="17" height="9" fill="#e8141b"/></svg>
  <p>I NEED<br><b>SIGN PLACEMENT ASAP</b></p>
  <svg class="stripe" viewBox="0 0 139 11" preserveAspectRatio="none"><path d="M0 11V5L139 0v11z" fill="#e8141b"/></svg>
</div>

<h2 class="packages-title abs">Choose Your Package</h2>

<div class="plan abs" style="left:140px">
  <svg class="plan-head" viewBox="0 0 83 42" preserveAspectRatio="none"><path d="M0 0h83v36Q60 42 42 36T0 38z" fill="#f3f3f3"/></svg>
  <div class="plan-name">5 SIGNS</div>
  <ul>
    <li><svg width="5" height="5" viewBox="0 0 10 10"><rect width="10" height="10" fill="#fde"/><path d="M2 5l2 2 4-5" fill="none" stroke="#e8141b" stroke-width="2"/></svg>Place signs strategically in best areas according to where the open house is located</li>
    <li><svg width="5" height="5" viewBox="0 0 10 10"><rect width="10" height="10" fill="#fde"/><path d="M2 5l2 2 4-5" fill="none" stroke="#e8141b" stroke-width="2"/></svg>Pick Up the signs after the open house</li>
    <li><svg width="5" height="5" viewBox="0 0 10 10"><rect width="10" height="10" fill="#fde"/><path d="M2 5l2 2 4-5" fill="none" stroke="#e8141b" stroke-width="2"/></svg>Store custom signs for you if needed</li>
  </ul>
  <div class="btn">SIGN UP</div>
  <p class="note">Sign Up For A Subscription And Get These Marketing Services For Free</p>
</div>
<div class="plan abs" style="left:228.5px">
  <svg class="plan-head" viewBox="0 0 83 42" preserveAspectRatio="none"><path d="M0 0h83v36Q60 42 42 36T0 38z" fill="#f3f3f3"/></svg>
  <div class="plan-name">10 SIGNS</div>
  <ul>
    <li><svg width="5" height="5" viewBox="0 0 10 10"><rect width="10" height="10" fill="#fde"/><path d="M2 5l2 2 4-5" fill="none" stroke="#e8141b" stroke-width="2"/></svg>Place signs strategically in best areas according to where the open house is located</li>
    <li><svg width="5" height="5" viewBox="0 0 10 10"><rect width="10" height="10" fill="#fde"/><path d="M2 5l2 2 4-5" fill="none" stroke="#e8141b" stroke-width="2"/></svg>Pick Up the signs after the open house</li>
    <li><svg width="5" height="5" viewBox="0 0 10 10"><rect width="10" height="10" fill="#fde"/><path d="M2 5l2 2 4-5" fill="none" stroke="#e8141b" stroke-width="2"/></svg>Store custom signs for you if needed</li>
  </ul>
  <div class="btn">SIGN UP</div>
  <p class="note">Sign Up For A Subscription And Get These Marketing Services For Free</p>
</div>
<div class="plan featured abs" style="left:317px">
  <svg class="plan-head" viewBox="0 0 83 42" preserveAspectRatio="none"><path d="M0 0h83v36Q60 42 42 36T0 38z" fill="#e8141b"/></svg>
  <div class="plan-name" style="color:#fff">15 SIGNS</div>
  <ul>
    <li><svg width="5" height="5" viewBox="0 0 10 10"><rect width="10" height="10" fill="#fde"/><path d="M2 5l2 2 4-5" fill="none" stroke="#e8141b" stroke-width="2"/></svg>Place signs strategically in best areas according to where the open house is located</li>
    <li><svg width="5" height="5" viewBox="0 0 10 10"><rect width="10" height="10" fill="#fde"/><path d="M2 5l2 2 4-5" fill="none" stroke="#e8141b" stroke-width="2"/></svg>Pick Up the signs after the open house</li>
    <li><svg width="5" height="5" viewBox="0 0 10 10"><rect width="10" height="10" fill="#fde"/><path d="M2 5l2 2 4-5" fill="none" stroke="#e8141b" stroke-width="2"/></svg>Store custom signs for you if needed</li>
  </ul>
  <div class="btn">SIGN UP</div>
  <p class="note">Sign Up For A Subscription And Get These Marketing Services For Free</p>
</div>
<div class="plan abs" style="left:405.5px">
  <svg class="plan-head" viewBox="0 0 83 42" preserveAspectRatio="none"><path d="M0 0h83v36Q60 42 42 36T0 38z" fill="#f3f3f3"/></svg>
  <div class="plan-name">20 SIGNS</div>
  <ul>
    <li><svg width="5" height="5" viewBox="0 0 10 10"><rect width="10" height="10" fill="#fde"/><path d="M2 5l2 2 4-5" fill="none" stroke="#e8141b" stroke-width="2"/></svg>Place signs strategically in best areas according to where the open house is located</li>
    <li><svg width="5" height="5" viewBox="0 0 10 10"><rect width="10" height="10" fill="#fde"/><path d="M2 5l2 2 4-5" fill="none" stroke="#e8141b" stroke-width="2"/></svg>Pick Up the signs after the open house</li>
    <li><svg width="5" height="5" viewBox="0 0 10 10"><rect width="10" height="10" fill="#fde"/><path d="M2 5l2 2 4-5" fill="none" stroke="#e8141b" stroke-width="2"/></svg>Store custom signs for you if needed</li>
  </ul>
  <div class="btn">SIGN UP</div>
  <p class="note">Sign Up For A Subscription And Get These Marketing Services For Free</p>
</div>
<div class="plan abs" style="left:494px">
  <svg class="plan-head" viewBox="0 0 83 42" preserveAspectRatio="none"><path d="M0 0h83v36Q60 42 42 36T0 38z" fill="#f3f3f3"/></svg>
  <div class="plan-name" style="color:#e8141b">25 SIGNS</div>
  <ul>
    <li><svg width="5" height="5" viewBox="0 0 10 10"><rect width="10" height="10" fill="#fde"/><path d="M2 5l2 2 4-5" fill="none" stroke="#e8141b" stroke-width="2"/></svg>Place signs strategically in best areas according to where the open house is located</li>
    <li><svg width="5" height="5" viewBox="0 0 10 10"><rect width="10" height="10" fill="#fde"/><path d="M2 5l2 2 4-5" fill="none" stroke="#e8141b" stroke-width="2"/></svg>Pick Up the signs after the open house</li>
    <li><svg width="5" height="5" viewBox="0 0 10 10"><rect width="10" height="10" fill="#fde"/><path d="M2 5l2 2 4-5" fill="none" stroke="#e8141b" stroke-width="2"/></svg>Store custom signs for you if needed</li>
  </ul>
  <div class="btn">SIGN UP</div>
  <p class="note">Sign Up For A Subscription And Get These Marketing Services For Free</p>
</div>

<h2 class="news-title abs">Latest News</h2>
<article class="news-item abs" style="top:898px">
  <div class="thumb" role="img" aria-label="Photo of a red open house sign on a lawn" style="background:linear-gradient(135deg,#c81d1f 0%,#b73a30 50%,#6d7a4a 100%)"></div>
  <div class="news-body">
    <h3>Lorem Ipsum charsets layouts</h3>
    <p class="news-meta">By <b>Wendell Marsh</b> | 03 Aug 2018</p>
    <p>Class aptent taciti sociosqu ad litora torquent per conubia himenaeos. Mauris in erat justo.</p>
  </div>
</article>
<article class="news-item abs" style="top:965px">
  <div class="thumb" role="img" aria-label="Photo of an agent greeting a couple at a front door" style="background:linear-gradient(135deg,#c9c4b8 0%,#8b7d6c 50%,#d8d2c6 100%)"></div>
  <div class="news-body">
    <h3>Lorem Ipsum charsets layouts</h3>
    <p class="news-meta">By <b>Wendell Marsh</b> | 03 Aug 2018</p>
    <p>Class aptent taciti sociosqu ad litora torquent per conubia himenaeos. Mauris in erat justo.</p>
  </div>
</article>

<h2 class="testimonials-title abs">Testimonials</h2>
<div class="quote-mark abs">&#8220;</div>
<p class="quote abs">Class aptent taciti sociosqu ad litora torquent per conubia nostra, per inceptos himenaeos. Mauris in condimentum sit amet a augue. Sed non neque elit. Sed ut imperdiet nisi. Proin condimentum fermentum nunc. Etiam pharetra, erat sed fermentum feugiat, velit mauris egestas quam, ut aliquam massa nisl quis neque. Suspendisse in orci enim. Mauris in condimentum sit amet a augue. Sed non fermentum feugiat, velit mauris egestas quam, neque elit.</p>
<div class="avatar abs" role="img" aria-label="Portrait photo of the reviewer"></div>
<div class="author abs"><b>- Jonah Pell</b><span>Lorem ipsum dolor</span></div>
<div class="dots abs"><i class="on"></i><i></i><i></i><i></i><i></i></div>

<div class="footer-col abs" style="left:140px">
  <h4>CONTACT INFORMATION</h4>
  <p>4410 Lorem ipsum dolor,<br>Suite 220, dosis, TX 70000</p>
  <p style="margin-top:9px">Phone: 1800 555 0178<br>Fax: 1800 555 0193<br>info@tallyporchhelpers.net</p>
</div>
<div class="footer-col abs" style="left:252px">
  <h4>QUICK LINKS</h4>
  <ul><li>› How It Works</li><li>› Service Area</li><li>› Pricing</li><li>› About Us</li><li>› FAQ</li></ul>
</div>
<div class="footer-col abs" style="left:327px">
  <h4>SOCIAL MEDIA</h4>
  <ul><li>▪ Circlespace</li><li>▪ Chirpline</li><li>▪ Workgrid</li><li>▪ Vidstream</li><li>▪ Snapframe</li></ul>
</div>
<div class="footer-col abs" style="left:401px">
  <h4>QUICK CONTACT</h4>
</div>
<div class="field abs" style="left:401px;top:1079px;width:87px;height:17px">Name</div>
<div class="field abs" style="left:490px;top:1079px;width:87px;height:17px">Email</div>
<div class="field abs" style="left:401px;top:1098px;width:176px;height:36px">Message</div>
<div class="send abs" style="left:401px;top:1136px;width:73px;height:16px">SEND A MESSAGE</div>
<p class="legal abs" style="left:140px">Copyright © 2018 Tally Porch Helpers</p>
<p class="legal abs" style="left:479px;color:#bbb">Terms of Use &nbsp;|&nbsp; Privacy &nbsp;|&nbsp; Sitemap</p>

</body>
</html>
```